VENTURE CAPITAL GROUP BUSINESS CARD DESIGN

Venture Capital Group based in SF looking for a bold business card design. No trendy colour explosion, 3D effects etc. Just "simple" optical effects. Works on your brain, keeps your eye focused and sticks to your mind.
Target Market(s)
Technology startups
Industry/Entity Type
Venture Capital
Contact Information for Business Card
DESMOND WHITLAKE
MANAGING PARTNER
187 FENWORTH ST SAN FRANCISCO, CA 94187
415.555.0142 O
415.555.0147 F
415.555.0193 C
desmond@veldtmoorcapital.ventures

```html
<!DOCTYPE html>
<html lang="en">
<head>
<meta charset="utf-8">
<title>Veldtmoor Capital Group – Business Cards</title>
<link href="https://fonts.googleapis.com/css2?family=Open+Sans:wght@400;600;700&display=swap" rel="stylesheet">
<style>
  :root {
    --page-bg: #e9e7e2;
    --card-white: #ffffff;
    --green-dark: #0f6a2c;
    --green-mid: #1f8a3b;
    --green-light: #4cb749;
    --text-grey: #6d6d6d;
    --text-dark: #3a3a3a;
    --rule-grey: #d6d6d6;
  }
  * { box-sizing: border-box; margin: 0; padding: 0; }
  html, body { width: 1200px; height: 950px; overflow: hidden; }
  body {
    background: var(--page-bg);
    font-family: "Open Sans", Arial, sans-serif;
    position: relative;
  }
  .card {
    position: absolute;
    left: 250px;
    width: 700px;
    height: 400px;
    border-radius: 22px;
    overflow: hidden;
    box-shadow: 0 10px 28px rgba(0,0,0,0.18);
  }
  /* Front */
  .card-front { top: 50px; background: var(--card-white); }
  .card-front .divider {
    position: absolute; left: 0; top: 0; width: 700px; height: 400px;
  }
  .contact-block {
    position: absolute; left: 350px; top: 48px; width: 330px;
  }
  .contact-name {
    font-weight: 700; font-size: 29px; color: var(--green-mid);
    line-height: 1.2;
  }
  .contact-title {
    font-size: 16px; color: var(--text-grey); margin-top: 2px;
  }
  .contact-address {
    font-size: 15px; color: var(--text-dark); margin-top: 12px; line-height: 1.45;
  }
  .contact-lines { list-style: none; margin-top: 12px; }
  .contact-lines li {
    display: flex; align-items: center; gap: 10px;
    font-size: 15px; color: var(--text-dark); line-height: 1.7;
    white-space: nowrap;
  }
  .contact-lines svg { width: 15px; height: 15px; flex: none; }
  .brand-front {
    position: absolute; left: 40px; top: 140px; width: 250px;
    display: flex; flex-direction: column; align-items: center; gap: 16px;
    text-align: center;
  }
  .brand-mark {
    width: 56px; height: 56px; border-radius: 50%; background: var(--green-mid);
  }
  .brand-name {
    font-weight: 600; font-size: 22px; color: var(--green-mid);
    letter-spacing: 1.5px; line-height: 1.2;
  }
  /* Back */
  .card-back {
    top: 500px;
    background: linear-gradient(135deg, var(--green-light) 0%, var(--green-mid) 50%, var(--green-dark) 100%);
  }
  .back-circle {
    position: absolute; left: 40px; top: 40px;
    width: 320px; height: 320px; border-radius: 50%;
    background: radial-gradient(circle at 40% 40%, #ffffff 0%, #f1f1f1 70%, #dcdcdc 100%);
  }
  .brand-back {
    position: absolute; left: 400px; top: 150px;
  }
  .brand-back .brand-name {
    color: var(--card-white); font-size: 30px;
  }
  .web-address {
    margin-top: 16px; font-size: 15px; color: var(--card-white);
  }
</style>
</head>
<body>

<section class="card card-front" aria-label="Business card front">
  <svg class="divider" viewBox="0 0 700 400" aria-hidden="true">
    <line x1="320" y1="40" x2="320" y2="360" stroke="var(--rule-grey)" stroke-width="1.2"/>
  </svg>

  <div class="brand-front">
    <span class="brand-mark" aria-hidden="true"></span>
    <span class="brand-name">VELDTMOOR<br>CAPITAL GROUP</span>
  </div>

  <div class="contact-block">
    <h1 class="contact-name">Desmond Whitlake</h1>
    <p class="contact-title">Managing Partner</p>
    <p class="contact-address">187 Fenworth St San Francisco<br>CA 94187</p>
    <ul class="contact-lines">
      <li>
        <svg viewBox="0 0 16 16" aria-label="Office"><path d="M3 1.5l3 3-1.5 2a9 9 0 0 0 5 5l2-1.5 3 3-2 2C6 14.5 1.5 10 1 3z" fill="var(--text-dark)"/></svg>
        415.555.0142
      </li>
      <li>
        <svg viewBox="0 0 16 16" aria-label="Fax"><rect x="2" y="6" width="12" height="8" rx="1" fill="var(--text-dark)"/><rect x="4" y="2" width="8" height="5" fill="none" stroke="var(--text-dark)" stroke-width="1.4"/></svg>
        415.555.0147
      </li>
      <li>
        <svg viewBox="0 0 16 16" aria-label="Mobile"><rect x="4" y="1" width="8" height="14" rx="1.5" fill="none" stroke="var(--text-dark)" stroke-width="1.6"/><circle cx="8" cy="12.5" r="1" fill="var(--text-dark)"/></svg>
        415.555.0193
      </li>
      <li>
        <svg viewBox="0 0 16 16" aria-label="Email"><rect x="1" y="3" width="14" height="10" rx="1" fill="var(--text-dark)"/><path d="M1.5 4l6.5 5 6.5-5" fill="none" stroke="#fff" stroke-width="1.3"/></svg>
        desmond@veldtmoorcapital.ventures
      </li>
    </ul>
  </div>
</section>

<section class="card card-back" aria-label="Business card back">
  <div class="back-circle" aria-hidden="true"></div>
  <div class="brand-back">
    <p class="brand-name">VELDTMOOR<br>CAPITAL GROUP</p>
    <p class="web-address">www.veldtmoorcapital.ventures</p>
  </div>
</section>

</body>
</html>
```